Modern Verdell Tree Care Website

I need a website for a full service Tree Care company. The company provides tree pruning, tree removal, tree preservation, emergency services, stump grinding, and emergency tree services.

Target Market(s)

Customers that need tree services

Industry/Entity Type

Landscaping, Tree Services

Coding

Coded - Design and coding required

Number of Pages Required

5+ page

Font styles to use
Sans Serif

Requirements
Must have
• Good clean design that showcases the services the company provides.
Nice to have
• Services page; contact form, blog, home page, about page

```html
<!DOCTYPE html>
<html lang="en">
<head>
<meta charset="utf-8">
<title>Verdell Tree Care</title>
<link href="https://fonts.googleapis.com/css2?family=Outfit:wght@500;600;700&family=Inter:wght@400;600;700&display=swap" rel="stylesheet">
<style>
:root{
  --green:#8cc63f;
  --tan:#c89a68;
  --orange:#f9ab3a;
  --blue:#1e88f0;
  --ink:#1b1b1b;
  --muted:#444;
  --footer:#eeeded;
  --white:#fff;
}
*{margin:0;padding:0;box-sizing:border-box}
html,body{width:1200px;height:1200px;overflow:hidden;background:var(--white)}
body{position:relative;font-family:"Inter",Arial,sans-serif;color:var(--ink)}
.page{position:absolute;left:431.7px;top:0;width:542px;height:1932px;transform:scale(.62112);transform-origin:0 0;overflow:hidden;background:var(--white)}
.abs{position:absolute}
h1,h2,h3{font-family:"Outfit",Arial,sans-serif;font-weight:600}
.photo{position:absolute}
p,li{font-size:4.2px;line-height:1.45}
ul{list-style:none}
ul li::before{content:"•";margin-right:3px}
.btn{position:absolute;border-radius:3px;font-size:3.6px;display:flex;align-items:center;justify-content:center;font-family:"Inter",Arial,sans-serif}
.btn-blue{background:var(--blue);color:var(--white)}
.btn-green{background:var(--green);color:var(--white)}
.btn-white{background:var(--white);color:var(--muted)}

/* hero */
.hero-svg{position:absolute;left:0;top:0}
.logo{position:absolute;left:28px;top:12px;display:flex;gap:4px;align-items:center}
.logo-mark{width:10px;height:10px;background:var(--orange)}
.logo-name{font-family:"Outfit",Arial,sans-serif;font-weight:600;color:var(--green);font-size:8.5px;line-height:1;letter-spacing:.5px}
.nav{position:absolute;top:13px;left:315px;display:flex;gap:15px;font-size:7.5px;color:var(--white);font-family:"Outfit",Arial,sans-serif;font-weight:500}
.hero-copy{position:absolute;left:233px;top:226px;width:190px;color:var(--white)}
.hero-copy h1{font-size:7.6px;margin-bottom:10px;font-weight:600}
.hero-copy p{font-size:3.4px;line-height:1.5}

/* services */
.services-head{position:absolute;top:355px;left:0;width:542px;text-align:center}
.services-head h2{font-size:13px}
.services-head p{width:222px;margin:3px auto 0;font-size:3.4px;color:var(--muted)}
.service{position:absolute;top:414px;width:110px;text-align:center}
.service .thumb{width:79px;height:79px;border-radius:50%;margin:0 auto}
.service h3{font-family:"Inter",Arial,sans-serif;font-weight:700;font-size:3.6px;margin-top:10px}
.service p{font-size:3.4px;color:var(--muted);margin-top:8px}

/* removal */
.removal-copy{position:absolute;left:233px;top:694px;width:218px;color:var(--white)}
.removal-copy h2{font-size:13.5px;color:var(--ink);margin-bottom:23px}
.removal-copy p,.removal-copy li{font-size:4.4px}
.removal-copy ul{padding-left:8px}
.projects{position:absolute;left:0;top:864px;width:542px;text-align:center}
.projects h2{font-size:12.5px;line-height:1.75}
.projects-body{position:absolute;left:152px;top:918px;width:282px;color:var(--white)}
.projects-body ul{padding-left:8px;color:#fff4dc}

/* photo strip */
.strip{position:absolute;top:1055px;left:0;width:542px;height:143px;display:flex}
.strip div{flex:1;height:100%}

/* green */
.green{position:absolute;top:1198px;left:0;width:542px;height:423px;background:var(--green)}
.care-copy{position:absolute;left:233px;top:1222px;width:240px}
.care-copy h2{font-size:10px;line-height:1.38;margin-bottom:12px}
.care-copy ul{padding-left:8px}
.why-copy{position:absolute;left:28px;top:1424px;width:232px}
.why-copy h2{font-size:10px;line-height:1.38;margin-bottom:16px}
.why-copy ul li{padding-left:6px;text-indent:-4px}

/* reviews */
.reviews-title{position:absolute;top:1636px;width:542px;text-align:center;font-family:"Inter",Arial,sans-serif;font-weight:700;font-size:8px}
.review{position:absolute;width:113px;background:var(--white);box-shadow:0 0 2px rgba(0,0,0,.08);padding:3px 5px}
.review .who{display:flex;justify-content:space-between;align-items:center;font-size:4px;color:var(--muted)}
.stars{color:var(--orange);font-size:7px;letter-spacing:-.3px}
.review h3{font-size:7px;line-height:1.2;margin:2px 0}
.review p{font-size:5.1px;line-height:1.6;color:var(--muted)}

/* footer */
.footer{position:absolute;top:1805px;left:0;width:542px;height:127px;background:var(--footer)}
.f-logo{position:absolute;left:68px;top:27px;display:flex;gap:3px;align-items:center}
.f-logo .logo-mark{width:8px;height:8px}
.f-logo .logo-name{font-size:7px}
.f-address{position:absolute;left:68px;top:50px;font-size:3.6px;font-weight:600;line-height:2.9}
.f-col{position:absolute;top:25px}
.f-col h4{font-family:"Outfit",Arial,sans-serif;font-weight:500;font-size:7.4px;margin-bottom:5px}
.f-col li{font-size:3.4px;font-weight:600;line-height:3;padding-left:3px}
.social{display:flex;gap:7px;margin-top:3px}
.social span{width:9px;height:9px;border-radius:50%;background:var(--ink)}
.cookie{position:absolute;bottom:13px;width:542px;text-align:center;font-size:3.3px;line-height:1.5}
</style>
</head>
<body>
<div class="page">

  <!-- hero -->
  <svg class="hero-svg" width="542" height="345" viewBox="0 0 542 345">
    <defs>
      <linearGradient id="heroPhoto" x1="0" y1="0" x2="1" y2="1">
        <stop offset="0" stop-color="#3f4a3a"/>
        <stop offset=".45" stop-color="#7a5a45"/>
        <stop offset=".8" stop-color="#9b6f52"/>
        <stop offset="1" stop-color="#6f4c38"/>
      </linearGradient>
      <linearGradient id="roundPhoto" x1="0" y1="0" x2="0" y2="1">
        <stop offset="0" stop-color="#7fb24a"/>
        <stop offset="1" stop-color="#4e7a34"/>
      </linearGradient>
    </defs>
    <path role="img" aria-label="Arborist cutting a tree stump with a chainsaw" d="M0 0H542V200C480 290 360 345 240 340C150 336 60 316 0 292Z" fill="url(#heroPhoto)"/>
    <path d="M0 248Q70 222 150 232L245 341C150 337 60 318 0 298Z" fill="var(--tan)"/>
    <path d="M82 318Q165 268 246 341C180 342 120 332 82 318Z" fill="var(--orange)"/>
    <circle role="img" aria-label="Arborist in a bucket lift trimming a leafy tree" cx="146" cy="248" r="68" fill="url(#roundPhoto)"/>
    <rect x="228" y="218" width="200" height="90" rx="4" fill="rgba(255,255,255,.08)"/>
  </svg>
  <div class="logo"><span class="logo-mark"></span><span class="logo-name">VERDELL<br>TREE CARE</span></div>
  <nav class="nav"><span>Home</span><span>About us</span><span>Services</span><span>Contact us</span></nav>
  <div class="hero-copy">
    <h1>Tree Pruning: for Health, for Beauty, for Safety</h1>
    <p>Expert pruning is one of the most valuable things you can do for the health and longevity of your trees. Proper pruning services by professional arborists help to preserve your trees' structural integrity, shape, health, and beauty. Responsible pruning and trimming also reduces the risk of falling tree limbs during severe weather, helping you safeguard the people, pets, and buildings on your property.</p>
  </div>
  <div class="btn btn-blue" style="left:297px;top:287px;width:42px;height:11px">Read More</div>

  <!-- services -->
  <div class="services-head">
    <h2>Services</h2>
    <p>Oakline Tree also offers emergency tree removal services when a tree or major limb falls suddenly and requires immediate clearance. Regardless of the circumstance, please do not attempt to remove a tree on your own. To do it safely requires careful</p>
  </div>
  <div class="service" style="left:32px">
    <div class="thumb" role="img" aria-label="Arborist in a bucket lift among green branches" style="background:#6ea845"></div>
    <h3>Tree Removal</h3>
    <p>Oakline Tree also offers emergency tree removal services when a tree or major limb falls suddenly and requires immediate clearance. Regardless of the circumstance, please do not attempt to remove a tree on your own. To do it safely requires careful techniques, specialized equipment, and qualified arborists. Tree removal should be left to the professionals.</p>
  </div>
  <div class="btn btn-green" style="left:69px;top:565px;width:35px;height:10px">Read More</div>
  <div class="service" style="left:154px">
    <div class="thumb" role="img" aria-label="Looking up into a tall tree canopy with a climber" style="background:#56718a"></div>
    <h3>Organic Tree Care</h3>
    <p>Oakline Tree also offers emergency tree removal services when a tree or major limb falls suddenly and requires immediate clearance. Regardless of the circumstance, please do not attempt to remove a tree on your own. To do it safely requires careful techniques, specialized equipment, and qualified arborists. Tree removal should be left to the professionals.</p>
  </div>
  <div class="btn btn-green" style="left:192px;top:565px;width:35px;height:10px">Read More</div>
  <div class="service" style="left:268px">
    <div class="thumb" role="img" aria-label="Aerial view of a yard and work trucks" style="background:#6a8a5a"></div>
    <h3>Tree Fertilization</h3>
    <p>Oakline Tree also offers emergency tree removal services when a tree or major limb falls suddenly and requires immediate clearance. Regardless of the circumstance, please do not attempt to remove a tree on your own. To do it safely requires careful techniques, specialized equipment, and qualified arborists. Tree removal should be left to the professionals.</p>
  </div>
  <div class="btn btn-green" style="left:315px;top:565px;width:35px;height:10px">Read More</div>
  <div class="service" style="left:378px">
    <div class="thumb" role="img" aria-label="Climber in orange gear high in a tree" style="background:#5f6e4c"></div>
    <h3>Tree Disease Treatment</h3>
    <p>Oakline Tree also offers emergency tree removal services when a tree or major limb falls suddenly and requires immediate clearance. Regardless of the circumstance, please do not attempt to remove a tree on your own. To do it safely requires careful techniques, specialized equipment, and qualified arborists. Tree removal should be left to the professionals.</p>
  </div>
  <div class="btn btn-green" style="left:438px;top:565px;width:35px;height:10px">Read More</div>

  <!-- removal & projects -->
  <svg class="abs" style="left:0;top:586px" width="542" height="469" viewBox="0 0 542 469">
    <defs>
      <linearGradient id="climbPhoto" x1="0" y1="0" x2="1" y2="1">
        <stop offset="0" stop-color="#6b5a44"/>
        <stop offset=".5" stop-color="#4f7a36"/>
        <stop offset="1" stop-color="#7e9a52"/>
      </linearGradient>
    </defs>
    <path d="M0 175C60 95 180 72 300 77C420 84 510 160 542 255V469H0Z" fill="var(--tan)"/>
    <path role="img" aria-label="Arborist in a green shirt and hard hat cutting branches high in a tree" d="M0 62L75 0H165L200 90L245 190L230 240L150 260L60 330L0 328Z" fill="url(#climbPhoto)"/>
    <path d="M0 355C80 265 200 238 310 239C420 242 505 300 542 380V469H0Z" fill="var(--orange)"/>
  </svg>
  <div class="removal-copy">
    <h2>Tree Removal</h2>
    <p>While we much prefer to focus our efforts on preserving trees, there are situations when removing a tree is the wisest course of action:</p>
    <ul>
      <li>It may be a "hazard tree" that has a structural defect that makes it likely to fail. When the hazard tree is close to buildings, walkways, and driveways, it poses significant risk to people, pets, and property.</li>
      <li>The tree threatens the health of other trees and shrubs nearby. Its removal can allow other plants a chance to develop and mature.</li>
    </ul>
    <p>Oakline Tree also offers emergency tree removal services when a tree or major limb falls suddenly and requires immediate clearance. Regardless of the circumstance, please do not attempt to remove a tree on your own. To do it safely requires careful techniques, specialized equipment, and qualified arborists. Tree removal should be left to the professionals.</p>
  </div>
  <div class="projects"><h2>Handling Projects of Any Size<br>We Serve a Diverse Range of Properties</h2></div>
  <div class="projects-body">
    <p>At Verdell Tree Care LLC, we pride ourselves on tackling projects of any size with professionalism and expertise. From residential homes to commercial properties, and public areas, we have extensive experience providing comprehensive tree care and property services. Our goal is to ensure the safety and well-being of your property. We are equipped with state-of-the-art equipment, including larger vehicles specifically designed for handling large-scale projects efficiently. With our team of skilled arborists, you can trust that your property is in good hands.</p>
    <ul>
      <li>Residential homes</li><li>Commercial properties</li><li>Golf clubs</li><li>Real estate investors</li><li>HOAs</li><li>Municipalities</li><li>Parks and public areas</li><li>Subcontract work for landscape and construction companies</li>
    </ul>
  </div>
  <div class="btn btn-white" style="left:253px;top:1025px;width:36px;height:11px">Read More</div>

  <!-- photo strip -->
  <div class="strip">
    <div role="img" aria-label="Bare tree beside a house roof" style="background:linear-gradient(#8fa3b8,#5b5f58)"></div>
    <div role="img" aria-label="Green lawn with tall trees" style="background:linear-gradient(#9fc07a,#3f6a2c)"></div>
    <div role="img" aria-label="Worker grinding a stump beside a white house" style="background:linear-gradient(#d6d8d6,#4f6a3a)"></div>
    <div role="img" aria-label="Wood chipper and work truck on a lawn" style="background:linear-gradient(#a8c4dc,#5f8a3e)"></div>
    <div role="img" aria-label="Tall pines and a bucket truck at a home" style="background:linear-gradient(#6f9ac0,#3a5a3a)"></div>
  </div>

  <!-- green section -->
  <div class="green"></div>
  <div class="photo" role="img" aria-label="Two arborists climbing a large tree in orange gear" style="left:28px;top:1216px;width:199px;height:172px;background:linear-gradient(135deg,#4f6e3a,#8a7a5e 60%,#3f5a2f)"></div>
  <div class="care-copy">
    <h2>Taking Care of Trees is Our Specialty<br>Tree Services in Brookfield, Westmere,<br>MA &amp; the Surrounding Areas</h2>
    <p>Are you looking for experienced and Certified Arborists to care for or remove trees on your property? Let your search end with Verdell Tree Care LLC. We're a trusted local, licensed, insured tree care company based in Brookfield, MA, serving the surrounding areas. With more than 15 years of experience, our arborists can provide various tree services, including those that require advanced training, like ornamental pruning. If you want tree care or tree removal done right, get in touch with us today.</p>
    <ul>
      <li>Tree Removal</li><li>Tree Pruning &amp; Maintenance</li><li>Stump Grinding</li><li>Storm Cleanup</li><li>Lawn Care</li><li>Emergency Tree Removal</li><li>Tree Planting</li>
    </ul>
  </div>
  <div class="btn btn-white" style="left:336px;top:1366px;width:35px;height:11px">Read More</div>
  <div class="why-copy">
    <h2>Why Choose Oakline Tree for Your Tree<br>Care and Maintenance?</h2>
    <ul>
      <li>We take tree care seriously. Your trees are as important to us as they are to you. We recruit the top professionals in the industry. Our certified arborists and technicians have a thorough understanding of soil chemistry and plant biology, and receive continual training in the most progressive methods used to maintain the safety and health of trees.</li>
      <li>Quality and safety are our watchwords. Our arborists adhere to best practices and national arboriculture care standards to ensure a safe and quality job. In fact, Oakline Tree was the first multi-state tree care company in the region to earn accreditation by the Northeast Arbor Guild for adhering to the highest quality service standards, business ethics, and customer satisfaction. Our accreditations include:</li>
      <li>Northeast Arbor Guild Accreditation</li>
      <li>Regional Arborist Board Certified Arborists</li>
      <li>State certification and licenses</li>
      <li>Full insurance coverage</li>
    </ul>
  </div>
  <div class="btn btn-white" style="left:131px;top:1568px;width:35px;height:11px">Read More</div>
  <div class="photo" role="img" aria-label="Arborist climbing among pine branches against a blue sky" style="left:275px;top:1421px;width:199px;height:172px;background:linear-gradient(135deg,#6f8fb0,#4f6a48 55%,#7d8f6a)"></div>

  <!-- reviews -->
  <div class="reviews-title">Customer Reviews</div>
  <div class="review" style="left:85px;top:1666px">
    <div class="who"><span>Marian Holt</span><span class="stars">★★★★★</span></div>
    <h3>Professionalism, Quality, Responsiveness</h3>
    <p>They were extremely knowledgeable &amp; careful in removing a very large failing oak tree from my front yard. Job was tricky due to positioning of tree near house and above ground utilities, as well as underground sprinkler system. Tree was very compromised after sustaining a direct lightening hit. Dan was at the job site the entire day while the tree was being taken down. Staff was very professional.</p>
  </div>
  <div class="review" style="left:213px;top:1692px">
    <div class="who"><span>Dana Pruitt</span><span class="stars">★★★★★</span></div>
    <p>Dan and his crew are professional and reliable! They removed a large tree in our yard and were very thorough, leaving the job looking neat and impressive. I'd highly recommend them for any tree work you may have.</p>
  </div>
  <div class="review" style="left:342px;top:1692px">
    <div class="who"><span>Rosa Delgado</span><span class="stars">★★★★★</span></div>
    <p>Dan and his crew had to remove my HUGE Maple tree in a very small drop zone. They did an amazing job. They were professional and quick and cleaned up afterwards. The price was very reasonable. I highly recommend Verdell Tree Care.</p>
  </div>

  <!-- footer -->
  <footer class="footer">
    <div class="f-logo"><span class="logo-mark"></span><span class="logo-name">VERDELL<br>TREE CARE</span></div>
    <div class="f-address">Brookfield, MA 01560<br>Phone: 555-010-2040<br>Email: info@verdelltreecare.com</div>
    <div class="f-col" style="left:192px"><h4>How Can We help You</h4><ul><li>Contact Us</li><li>Request Estimate</li></ul></div>
    <div class="f-col" style="left:315px"><h4>Our Company</h4><ul><li>About Us</li><li>Browse All Services</li></ul></div>
    <div class="f-col" style="left:397px"><h4>Follow us</h4><div class="social"><span></span><span></span><span></span><span></span></div></div>
    <div class="cookie">This site uses cookies to improve your experience.<br>By continuing to use our site, you agree to our Privacy Policy and Terms of Use.</div>
  </footer>
</div>
</body>
</html>
```